Timber Crest Construction Needs business card

Hey we are in need of business card designs. I have upload our logo as a guideline, but free feel to run with it or come up with something unique.
Pls have fun with it and be creative. the name says it all!
i will give some directions after i see a few entries..
Updates
Logo source file has been uploaded..
Hey because of the logo is so colourful already.
Can we have a few submissions with less colour.
Also we are looking for clever/hidden/descriptive business card.

```html
<!DOCTYPE html>
<html lang="en">
<head>
<meta charset="utf-8">
<title>Timber Crest Construction – Business Card</title>
<link href="https://fonts.googleapis.com/css2?family=Questrial&display=swap" rel="stylesheet">
<style>
  :root {
    --backdrop: #237f06;
    --card-dark: #000000;
    --card-light: #ffffff;
    --ink: #222222;
    --ink-soft: #333333;
    --accent-red: #ed1c24;
    --brand-grey: #8c8c8c;
    --block-blue: #0079c8;
    --block-green: #008c45;
    --block-yellow: #ffcb05;
    --block-grey: #3a3a3c;
  }
  * { margin: 0; padding: 0; box-sizing: border-box; }
  html, body { width: 1200px; height: 1200px; overflow: hidden; }
  body {
    background: var(--backdrop);
    font-family: "Questrial", "Century Gothic", sans-serif;
    position: relative;
  }
  .card {
    position: absolute;
    left: 212px;
    width: 800px;
    height: 445px;
    overflow: hidden;
  }
  .card--front { top: 130px; background: var(--card-dark); }
  .card--back { top: 641px; background: var(--card-light); }

  .block-decoration { position: absolute; }
  .card--front .block-decoration {
    left: 0; top: 0; width: 328px; height: 445px;
    background: linear-gradient(160deg, var(--block-grey) 0%, var(--block-blue) 30%, var(--accent-red) 55%, var(--block-yellow) 75%, var(--block-green) 100%);
    opacity: 0.85;
  }
  .card--back .block-decoration {
    left: 473px; top: 0; width: 319px; height: 445px;
    background: linear-gradient(200deg, var(--block-yellow) 0%, var(--accent-red) 30%, var(--block-blue) 60%, var(--block-green) 85%, var(--block-grey) 100%);
    opacity: 0.85;
  }

  .brand-name {
    position: absolute;
    left: 350px; top: 244px; width: 356px;
    text-align: center;
    color: var(--brand-grey);
    font-size: 29px;
    line-height: 1.15;
    letter-spacing: 2px;
  }

  .contact-person { position: absolute; left: 89px; top: 120px; }
  .person-name {
    font-size: 16px; font-weight: 700; letter-spacing: 3.5px;
    color: var(--ink);
  }
  .person-role {
    margin-top: 3px;
    font-size: 14px; letter-spacing: 2.5px;
    color: var(--accent-red);
  }
  .address {
    position: absolute; left: 89px; top: 202px;
    font-size: 14px; letter-spacing: 2.4px; line-height: 21px;
    color: var(--ink-soft);
  }
  .contact-list {
    position: absolute; left: 89px; top: 280px;
    list-style: none;
  }
  .contact-list li {
    display: flex; align-items: center;
    height: 25.3px;
    font-size: 14px; letter-spacing: 2.4px;
    color: var(--ink-soft);
  }
  .contact-list svg {
    width: 16px; height: 16px; margin-right: 20px;
    fill: none; stroke: var(--accent-red); stroke-width: 1.6;
  }
</style>
</head>
<body>

  <section class="card card--front" aria-label="Business card front">
    <div class="block-decoration" role="img" aria-label="Large coloured building-block decoration"></div>
    <p class="brand-name">TIMBER CREST<br>CONSTRUCTION</p>
  </section>

  <section class="card card--back" aria-label="Business card back">
    <div class="contact-person">
      <p class="person-name">MARLA VENN</p>
      <p class="person-role">DIRECTOR</p>
    </div>
    <p class="address">SHOP 3, 218-222 HARBOUR<br>ROAD WESTBROOK NORTH</p>
    <ul class="contact-list">
      <li>
        <svg viewBox="0 0 16 16" aria-hidden="true"><path d="M2 6c0-2 3-3 6-3s6 1 6 3l-2 1-1-2H5L4 7z"/><rect x="4" y="8" width="8" height="5" rx="1"/></svg>
        5310 2847
      </li>
      <li>
        <svg viewBox="0 0 16 16" aria-hidden="true"><rect x="4" y="2" width="8" height="4"/><rect x="2" y="6" width="12" height="5" rx="1"/><rect x="4" y="10" width="8" height="4"/></svg>
        5310 2849
      </li>
      <li>
        <svg viewBox="0 0 16 16" aria-hidden="true"><rect x="2" y="4" width="12" height="8"/><path d="M2 4l6 5 6-5"/></svg>
        marla@timbercrestbuild.com
      </li>
      <li>
        <svg viewBox="0 0 16 16" aria-hidden="true"><circle cx="8" cy="8" r="6"/><path d="M2 8h12M8 2c3 3 3 9 0 12M8 2c-3 3-3 9 0 12"/></svg>
        www.timbercrestbuild.com
      </li>
    </ul>
    <div class="block-decoration" role="img" aria-label="Coloured building-block decoration rising from the bottom edge"></div>
  </section>

</body>
</html>
```